Heron Dusk business card design

I make handmade colourful women's beaded jewellery (necklaces and earnings).
I require a business card to be designed to truly reflect my jewellery, that is, it is different and stands out.
I would like the business card to look creative, arty, gentle and feminine and fit in with the look of my website and logo (already developed).
I would like the business card to have strong use of the water reeds that are flowing in the wind (please see the banner image on my website www.herondusk.net and attached files).

Target Market(s)

Women who are fashion conscious, hip and funky. My audience like things that are a little different and stand out in a crowd.These women are aged in their 20's-40's.

Industry/Entity Type

Jewelry

Contact Information for Business Card

Please include the following items:
1) my logo: Heron Dusk
2) my name, address and phone number: Darla Fontenot, Sydney, Australia, 0498 315 270
3) my web details: www.herondusk.net, info@herondusk.net, www.facebook.com/herondusk

Font styles to use
Other font styles liked:
• Remachine Script

Requirements
Must have
• My business card must have the following:
• 1) my personal details including all my website contacts (see above).
• 2) Heron Dusk logo
• 3) Reeds flowing in the wind (see my banner image on my website www.herondusk.net or see attached files).
Nice to have
• A sunrise in the background (rising over water)
• I would prefer that the colour scheme to fit with the Heron Dusk logo, that is the colours of an early morning sunrise i.e yellows, oranges. The use of black and white is fine.
Should not have
• I do not like a commercial manufactured look with hard edges. I would like a look that is soft and reflects an artistic, creative and independent business.

```html
<!DOCTYPE html>
<html lang="en">
<head>
<meta charset="utf-8">
<title>Heron Dusk – Business Card</title>
<link href="https://fonts.googleapis.com/css2?family=Open+Sans:wght@400;600&display=swap" rel="stylesheet">
<style>
  :root {
    --backdrop: #e9e5df;
    --card-light: #ffffff;
    --card-dark: #2a2929;
    --sun: #f7b718;
    --sun-deep: #f39a12;
    --ink: #262626;
    --paper-text: #ffffff;
    --muted-line: #b9b9b9;
    --dot: #9a9a9a;
  }
  * { box-sizing: border-box; margin: 0; padding: 0; }
  html, body {
    width: 1200px; height: 950px; overflow: hidden;
    background: var(--backdrop);
    font-family: "Open Sans", Arial, sans-serif;
  }
  .sheet {
    width: 1200px; height: 950px;
    display: flex; flex-direction: column; align-items: center; justify-content: center;
    gap: 30px;
  }
  .card {
    width: 770px; height: 440px; border-radius: 26px;
    position: relative; overflow: hidden;
    box-shadow: 0 6px 18px rgba(0,0,0,0.18);
  }

  /* Front */
  .card-front { background: var(--card-light); }
  .front-logo {
    position: absolute; left: 0; right: 0; top: 120px;
    display: flex; align-items: center; justify-content: center; gap: 18px;
  }
  .logo-disc {
    width: 96px; height: 96px; border-radius: 50%;
    background: radial-gradient(circle at 50% 40%, #ffd84a, var(--sun) 60%, var(--sun-deep));
  }
  .logo-name {
    font-family: "Open Sans", Arial, sans-serif;
    font-weight: 600; font-size: 46px; color: var(--ink);
  }
  .front-swoosh { position: absolute; left: 0; top: 0; }
  .social-row {
    position: absolute; left: 50%; top: 318px; transform: translateX(-50%);
    display: flex; gap: 9px;
  }
  .social-dot { width: 22px; height: 22px; border-radius: 50%; background: var(--dot); }

  /* Back */
  .card-back { background: var(--card-dark); color: var(--paper-text); }
  .edge-tab {
    position: absolute; left: -22px; top: 150px;
    width: 44px; height: 44px; border-radius: 50%; background: var(--sun);
  }
  .holder { position: absolute; left: 48px; top: 146px; }
  .holder-name { color: var(--sun); font-weight: 600; font-size: 25px; line-height: 1.2; }
  .holder-role { font-size: 18px; margin-top: 2px; }
  .address { position: absolute; left: 48px; top: 250px; font-size: 17px; line-height: 1.35; }
  .contacts { position: absolute; left: 48px; top: 322px; list-style: none; font-size: 17px; }
  .contacts li { display: flex; align-items: center; gap: 10px; height: 24px; }
  .contacts svg { width: 17px; height: 17px; flex: none; }
  .square-mark { width: 15px; height: 15px; background: var(--sun); border-radius: 2px; flex: none; margin: 0 1px; }
  .back-logo {
    position: absolute; right: 46px; top: 60px;
    display: flex; flex-direction: column; align-items: center; gap: 18px;
  }
  .back-logo .logo-disc { width: 250px; height: 250px; border: 6px solid #ffffff; }
  .back-logo .logo-name { color: var(--paper-text); font-size: 48px; }
</style>
</head>
<body>
<main class="sheet">

  <section class="card card-front" aria-label="Card front">
    <div class="front-logo">
      <div class="logo-disc" aria-hidden="true"></div>
      <span class="logo-name">Heron Dusk</span>
    </div>
    <svg class="front-swoosh" width="770" height="440" aria-hidden="true">
      <path d="M150 360 Q385 320 620 300" fill="none" stroke="var(--muted-line)" stroke-width="2"/>
    </svg>
    <div class="social-row" aria-hidden="true">
      <span class="social-dot"></span><span class="social-dot"></span>
      <span class="social-dot"></span><span class="social-dot"></span>
    </div>
  </section>

  <section class="card card-back" aria-label="Card back">
    <div class="edge-tab" aria-hidden="true"></div>
    <div class="holder">
      <p class="holder-name">Mara Vell</p>
      <p class="holder-role">President</p>
    </div>
    <p class="address">Darla Fontenot<br>Sydney, Australia</p>
    <ul class="contacts">
      <li>
        <svg viewBox="0 0 20 20" aria-hidden="true"><path fill="var(--sun)" d="M5 2l3 4-2 2c1 3 3 5 6 6l2-2 4 3-2 3C9 18 2 11 2 4z"/></svg>
        0498 315 270
      </li>
      <li>
        <svg viewBox="0 0 20 20" aria-hidden="true"><rect x="1" y="4" width="18" height="12" rx="1.5" fill="var(--sun)"/><path d="M2 5l8 6 8-6" fill="none" stroke="var(--card-dark)" stroke-width="1.6"/></svg>
        info@herondusk.net
      </li>
      <li>
        <svg viewBox="0 0 20 20" aria-hidden="true"><circle cx="10" cy="10" r="8" fill="var(--sun)"/><circle cx="10" cy="10" r="3" fill="var(--card-dark)"/></svg>
        www.herondusk.net
      </li>
      <li>
        <span class="square-mark" aria-hidden="true"></span>
        herondusk
      </li>
    </ul>
    <div class="back-logo">
      <div class="logo-disc" aria-hidden="true"></div>
      <span class="logo-name">Heron Dusk</span>
    </div>
  </section>

</main>
</body>
</html>
```